Logo, Web and Mobile Designs for enterprise social media platform

All the details are in the attached document, please start reading the scope document first which explains what is this project about and the details about the needed deliverables, after that please read the UI_Requirements document which will detail what is expected regarding the coded web version since this is a coded contest, it is very important that you meet the UI requirements or suggest something else but we will need to agree first before working on the coded version

Good Luck

Target Market(s)

Enterprise Social Media

Industry/Entity Type

Media

Coding

Coded - Design and coding required

Number of Pages Required

5+ page

Font styles to use
Sans Serif

Requirements
Must have
• All the must haves are listed in the scope document so please check before you start

```html
<!DOCTYPE html>
<html lang="en">
<head>
<meta charset="utf-8">
<title>Teamora – Sponsor Details</title>
<link href="https://fonts.googleapis.com/css2?family=Roboto:wght@300;400;500&display=swap" rel="stylesheet">
<style>
:root{
  --page-bg:#ececec;
  --header-bg:#f7f7f7;
  --line:#dedede;
  --text:#555;
  --brand:#1d8ab8;
  --accent:#0c84c9;
  --orange:#f39c12;
  --white:#fff;
  --panel-head:#f5f6f8;
  --footer:#1d8ab8;
  --error:#e00;
}
*{box-sizing:border-box;margin:0;padding:0}
html,body{width:1200px;height:955px;overflow:hidden}
body{font-family:'Roboto',sans-serif;background:var(--page-bg);color:var(--text);position:relative}
.abs{position:absolute}
.topbar{left:0;top:0;width:1200px;height:70px;background:var(--header-bg);border-bottom:1px solid var(--line)}
.topbar .divider{top:0;width:1px;height:70px;background:var(--line)}
.menu-toggle{left:101px;top:28px}
.brand{left:168px;top:15px;display:flex;align-items:center;gap:8px}
.brand-dot{width:38px;height:38px;border-radius:50%;background:var(--orange)}
.brand-name{font-size:31px;font-weight:500;color:var(--brand)}
.user{left:746px;top:18px;display:flex;align-items:center;gap:12px}
.avatar{width:34px;height:34px;border-radius:50%;background:linear-gradient(#777,#333)}
.user-name{font-size:16.5px;color:var(--text)}
.badge{width:20px;height:16px;border-radius:8px;color:#fff;font-size:11px;text-align:center;line-height:16px}
.card{left:99px;top:105px;width:1001px;height:658px;background:var(--white);border:1px solid var(--line)}
.sidebar{left:0;top:0;width:278px;height:656px;background:#f3f3f3;border-right:1px solid #e0e0e0}
.side-main{display:flex;align-items:center;padding-left:17px;gap:14px;font-size:15.5px;color:#444;border-bottom:2px solid #e6e6e6}
.side-list{margin-top:18px;list-style:none}
.side-list li{height:32.6px;display:flex;align-items:center;padding-left:21px;gap:14px;font-size:16.3px;color:#555;border-bottom:1px solid #e4e4e4;font-weight:300}
.side-list li.active{color:var(--accent);font-weight:500}
.panel{left:310px;top:38px;width:661px;height:583px;border:1px solid #eaeaea;background:var(--white)}
.panel-head{height:50px;background:var(--panel-head);border-bottom:1px solid #e4e4e4;display:flex;align-items:center;padding-left:22px;gap:12px;font-size:15.5px;color:#444}
.label{font-size:14.5px;color:#555;font-weight:300;line-height:17px}
.field{border:1px solid #dcdcdc;background:#fff;font-size:11px;color:#444;display:flex;align-items:center;padding-left:14px;justify-content:space-between;padding-right:12px}
.field.error{color:var(--error)}
.plus{background:var(--accent);display:flex;align-items:center;justify-content:center}
.submit{background:var(--accent);color:#fff;font-size:16px;font-weight:400;display:flex;align-items:center;justify-content:center;border-radius:2px}
.footer{left:0;top:807px;width:1200px;height:148px;background:var(--footer);color:#fff;text-align:center}
.social{position:absolute;top:29px;left:513px;display:flex;gap:12px}
.social span{width:24px;height:24px;background:#fff;border-radius:4px}
.foot-links{position:absolute;top:71px;width:100%;font-size:14.5px;font-weight:300;line-height:17px}
.foot-links i{font-style:normal;margin:0 10px}
.copyright{position:absolute;top:101px;width:100%;font-size:14.5px;line-height:17px}
</style>
</head>
<body>
<header class="topbar abs">
  <svg class="menu-toggle abs" width="18" height="16" viewBox="0 0 18 16"><rect y="1" width="18" height="3" fill="#777"/><rect y="7" width="18" height="3" fill="#777"/><rect y="13" width="18" height="3" fill="#777"/></svg>
  <div class="divider abs" style="left:144px"></div>
  <div class="brand abs"><span class="brand-dot"></span><span class="brand-name">Teamora</span></div>
  <div class="user abs"><span class="avatar" role="img" aria-label="User profile photo"></span><span class="user-name">Marek Vossberg</span>
    <svg width="12" height="8"><path d="M0 0h12L6 8z" fill="#555"/></svg></div>
  <div class="divider abs" style="left:922px"></div>
  <div class="divider abs" style="left:991px"></div>
  <div class="divider abs" style="left:1051px"></div>
  <svg class="abs" style="left:946px;top:26px" width="20" height="18"><rect width="20" height="4" fill="#666"/><rect y="7" width="20" height="4" fill="#666"/><rect y="14" width="12" height="4" fill="#666"/></svg>
  <div class="badge abs" style="left:957px;top:16px;background:var(--orange)">8</div>
  <svg class="abs" style="left:1011px;top:26px" width="20" height="20"><circle cx="8" cy="8" r="6" fill="none" stroke="#666" stroke-width="2.5"/><path d="M12.5 12.5l6 6" stroke="#666" stroke-width="3"/></svg>
  <svg class="abs" style="left:1073px;top:26px" width="18" height="20"><path d="M9 1c-4 0-6 3-6 6v5l-2 3h16l-2-3V7c0-3-2-6-6-6z" fill="#666"/><circle cx="9" cy="18" r="2" fill="#666"/></svg>
  <div class="badge abs" style="left:1079px;top:16px;background:var(--accent)">8</div>
</header>

<main class="card abs">
  <nav class="sidebar abs">
    <div class="side-main" style="height:58px"><svg width="15" height="13"><rect width="7" height="6" fill="#1d8ab8"/><rect x="8" width="7" height="6" fill="#1d8ab8"/><rect y="7" width="7" height="6" fill="#1d8ab8"/><rect x="8" y="7" width="7" height="6" fill="#1d8ab8"/></svg>VIEW DASHBOARD</div>
    <div class="side-main" style="height:52px"><svg width="15" height="15"><rect x="1" y="2" width="13" height="12" fill="none" stroke="#1d8ab8" stroke-width="2"/><rect x="1" y="2" width="13" height="3" fill="#1d8ab8"/></svg>VIEW EVENT</div>
    <ul class="side-list">
      <li><svg width="7" height="10"><path d="M1 1l4 4-4 4" fill="none" stroke="currentColor" stroke-width="1.4"/></svg><span>About Us</span></li>
      <li><svg width="7" height="10"><path d="M1 1l4 4-4 4" fill="none" stroke="currentColor" stroke-width="1.4"/></svg><span>Speakers</span></li>
      <li><svg width="7" height="10"><path d="M1 1l4 4-4 4" fill="none" stroke="currentColor" stroke-width="1.4"/></svg><span>Track</span></li>
      <li><svg width="7" height="10"><path d="M1 1l4 4-4 4" fill="none" stroke="currentColor" stroke-width="1.4"/></svg><span>Sessions</span></li>
      <li><svg width="7" height="10"><path d="M1 1l4 4-4 4" fill="none" stroke="currentColor" stroke-width="1.4"/></svg><span>Tickets</span></li>
      <li><svg width="7" height="10"><path d="M1 1l4 4-4 4" fill="none" stroke="currentColor" stroke-width="1.4"/></svg><span>Organizers</span></li>
      <li class="active"><svg width="7" height="10"><path d="M1 1l4 4-4 4" fill="none" stroke="currentColor" stroke-width="1.4"/></svg><span>SPONSORS</span></li>
      <li><svg width="7" height="10"><path d="M1 1l4 4-4 4" fill="none" stroke="currentColor" stroke-width="1.4"/></svg><span>Exhibitor</span></li>
      <li><svg width="7" height="10"><path d="M1 1l4 4-4 4" fill="none" stroke="currentColor" stroke-width="1.4"/></svg><span>Security</span></li>
      <li><svg width="7" height="10"><path d="M1 1l4 4-4 4" fill="none" stroke="currentColor" stroke-width="1.4"/></svg><span>Members</span></li>
    </ul>
  </nav>

  <section class="panel abs">
    <div class="panel-head"><svg width="13" height="14"><circle cx="6.5" cy="4" r="4" fill="#555"/><path d="M0 14c0-5 3-6 6.5-6S13 9 13 14z" fill="#555"/></svg>SPONSOR DETAILS</div>
    <div class="label abs" style="left:22px;top:95px">Sponsor Name :</div>
    <div class="field error abs" style="left:186px;top:84px;width:452px;height:39px">This is a required field</div>
    <div class="label abs" style="left:22px;top:142px">Upload Sponsor Photo :</div>
    <svg class="abs" style="left:195px;top:144px" width="18" height="13"><path d="M4 13a4 4 0 010-8 6 6 0 0111 1 3.5 3.5 0 010 7z" fill="var(--accent)"/><path d="M9 4l3 4h-2v3H8V8H6z" fill="#fff"/></svg>
    <div class="label abs" style="left:22px;top:190px">Sponsorship Type :</div>
    <div class="field abs" style="left:186px;top:179px;width:448px;height:39px"></div>
    <div class="label abs" style="left:22px;top:250px">Sponsor Description :</div>
    <div class="field abs" style="left:186px;top:239px;width:452px;height:88px"></div>
    <div class="label abs" style="left:20px;top:359px">Phones :</div>
    <div class="field abs" style="left:185px;top:349px;width:196px;height:39px">Enter Phone</div>
    <div class="plus abs" style="left:404px;top:358px;width:21px;height:21px"><svg width="8" height="8"><path d="M3 0h2v8H3zM0 3h8v2H0z" fill="#fff"/></svg></div>
    <div class="label abs" style="left:22px;top:412px">Sponsor Social Links :</div>
    <div class="field abs" style="left:187px;top:401px;width:196px;height:39px">Select Link Type<svg width="8" height="5"><path d="M0 0l4 4 4-4" fill="none" stroke="#444"/></svg></div>
    <div class="field abs" style="left:393px;top:401px;width:188px;height:39px">http://example<svg width="8" height="5"><path d="M0 0l4 4 4-4" fill="none" stroke="#444"/></svg></div>
    <div class="plus abs" style="left:593px;top:401px;width:42px;height:39px"><svg width="14" height="14"><path d="M5 0h4v14H5zM0 5h14v4H0z" fill="#fff"/></svg></div>
    <div class="label abs" style="left:22px;top:472px">Sponsor External Links :</div>
    <div class="field abs" style="left:187px;top:461px;width:196px;height:39px">Enter link Title<svg width="8" height="5"><path d="M0 0l4 4 4-4" fill="none" stroke="#444"/></svg></div>
    <div class="field abs" style="left:393px;top:461px;width:188px;height:39px">http://example<svg width="8" height="5"><path d="M0 0l4 4 4-4" fill="none" stroke="#444"/></svg></div>
    <div class="plus abs" style="left:593px;top:461px;width:42px;height:39px"><svg width="14" height="14"><path d="M5 0h4v14H5zM0 5h14v4H0z" fill="#fff"/></svg></div>
    <div class="submit abs" style="left:186px;top:524px;width:161px;height:36px">ADD SPONSOR</div>
  </section>
</main>

<footer class="footer abs">
  <div class="social"><span></span><span></span><span></span><span></span><span></span></div>
  <div class="foot-links">Home<i>/</i>Contact<i>/</i>Topics<i>/</i>Posts and Comments<i>/</i>Discussion<i>/</i>Videos Links</div>
  <div class="copyright">Copyright @ 2015 - 2015.Teamora. All Rights Reserved.</div>
</footer>
</body>
</html>
```